Musical download and streaming website

hello designers, I want to start up a musical website where users can download and rate music of different genres such as RnB, Hip hop, rock, afro-pop. This website should be attractive and contemporary. There will be a search column for different songs. Music files will be mp3, mwa, and others. I like blue, gold, pink and indigo colors. My website should resemble http://tunovalt.com. There should be good imaginary of music stars on my website.

```html
<!DOCTYPE html>
<html lang="en">
<head>
<meta charset="utf-8">
<title>Lumen Music</title>
<link href="https://fonts.googleapis.com/css2?family=Raleway:wght@500;600;700;800&family=Open+Sans:wght@400;600;700&display=swap" rel="stylesheet">
<style>
:root{
  --pink:#c94f94;
  --blue:#3b9bd8;
  --blue-dark:#2f87c2;
  --purple:#8a63c9;
  --purple-dark:#6f4bae;
  --orange:#e0963c;
  --orange-dark:#c57c26;
  --gold:#e6a817;
  --ink:#222;
  --text:#444;
  --muted:#888;
  --line:#d9dde2;
  --panel:#f4f8fb;
  --sky-top:#d6edf9;
  --sky-bottom:#f2f9fc;
}
*{box-sizing:border-box;margin:0;padding:0}
html,body{width:1200px;height:2557px;overflow:hidden}
body{position:relative;font-family:"Open Sans",sans-serif;color:var(--text);
  background:linear-gradient(var(--sky-top),var(--sky-bottom) 60%,#eef7fb)}
.top-stripe{position:absolute;top:0;left:0;width:1200px;height:4px;
  background:linear-gradient(90deg,var(--pink),var(--gold),var(--blue))}
.site-header{position:absolute;top:4px;left:0;width:1200px;height:78px;background:#fff;
  box-shadow:0 2px 4px rgba(0,0,0,.08)}
.brand{position:absolute;left:97px;top:18px;font-family:"Raleway",sans-serif;font-weight:700;
  font-size:32px;color:var(--purple);letter-spacing:1px}
.main-nav{position:absolute;left:440px;top:30px;display:flex;gap:33px;
  font-family:"Raleway",sans-serif;font-weight:700;font-size:14px;color:#333}
.btn{position:absolute;top:20px;height:37px;border-radius:3px;color:#fff;font-family:"Raleway",sans-serif;
  font-weight:700;font-size:14px;display:flex;align-items:center;justify-content:center}
.btn-login{left:922px;width:84px;background:linear-gradient(var(--blue),var(--blue-dark))}
.btn-signup{left:1018px;width:82px;background:var(--pink)}

.page{position:absolute;left:95px;top:124px;width:1010px;height:2055px;background:#fff;
  box-shadow:0 0 6px rgba(0,0,0,.12)}
.genre-tabs{display:flex;height:48px;background:var(--blue);font-family:"Raleway",sans-serif;
  font-weight:700;font-size:15px;color:#fff}
.genre-tabs span{display:flex;align-items:center;padding:0 25px}
.genre-tabs .active{background:var(--pink);width:102px;justify-content:center;padding:0}
.genre-tabs .spread{flex:1;justify-content:center;padding:0}
.search-bar{position:absolute;top:48px;left:0;width:1010px;height:84px;background:var(--panel);
  display:flex;align-items:center;padding-left:24px}
.radio{display:flex;align-items:center;gap:10px;margin-right:30px;font-family:"Raleway",sans-serif;
  font-weight:700;font-size:15px;color:#333}
.radio i{width:20px;height:20px;border:2px solid #bbb;border-radius:50%;position:relative}
.radio.checked{color:var(--pink)}
.radio.checked i{border-color:var(--pink)}
.radio.checked i::after{content:"";position:absolute;left:3px;top:3px;width:10px;height:10px;
  border-radius:50%;background:var(--pink)}
.search-input{position:absolute;left:331px;top:20px;width:540px;height:44px;background:#fff;border:1px solid var(--line)}
.search-btn{position:absolute;left:870px;top:20px;width:113px;height:44px;background:var(--pink);color:#fff;
  font-family:"Raleway",sans-serif;font-weight:700;font-size:15px;display:flex;align-items:center;justify-content:center}
.alphabet{position:absolute;top:156px;left:22px;display:flex;align-items:center;font-size:14px;color:#444}
.alphabet .letters{display:flex;gap:12.6px;margin-left:22px;font-weight:700;font-style:italic;font-size:15px;color:#111}

.section-bar{position:absolute;left:0;width:1010px;height:50px;color:#fff;font-family:"Raleway",sans-serif;
  font-weight:700;font-size:19px;display:flex;align-items:center;padding-left:25px}
.section-bar .arrows{position:absolute;right:0;top:0;width:84px;height:50px;display:flex;align-items:center;
  justify-content:center;gap:16px;font-size:24px}
.bar-newest{top:215px;background:var(--purple)}
.bar-newest .arrows{background:var(--purple-dark)}
.bar-videos{top:534px;background:var(--orange)}
.bar-videos .arrows{background:var(--orange-dark)}
.track-row{position:absolute;left:26px;display:flex;gap:26px}
.row-newest{top:294px}
.row-videos{top:611px}
.track{width:170px}
.track .art{width:170px;height:143px}
.track h4{margin-top:16px;font-family:"Raleway",sans-serif;font-weight:700;font-size:15px;color:#222;white-space:nowrap}
.track h4 small{font-family:"Open Sans",sans-serif;font-weight:400;font-size:12px;color:#444}
.rating{font-size:12px;color:var(--muted);margin-top:2px}
.rating b{color:var(--gold);font-weight:400;letter-spacing:1px;margin-right:4px}
.divider{position:absolute;left:26px;top:848px;width:957px;height:1px;background:var(--line)}

.list-box{position:absolute;top:889px;width:464px;height:372px;border:1px solid #cfd4d9}
.box-artists{left:26px}
.box-songs{left:519px}
.list-box h3{height:46px;border-bottom:1px solid #cfd4d9;padding:12px 18px;font-family:"Raleway",sans-serif;
  font-weight:700;font-size:19px;color:#222}
.list-box .cols{display:flex;padding:16px 0 0 31px}
.list-box ul{list-style:none;width:148px;font-size:13px;color:#333}
.list-box li{height:31.7px;display:flex;align-items:center;white-space:nowrap}
.list-box li::before{content:"➜";color:var(--blue);font-size:15px;margin-right:12px}

.welcome{position:absolute;left:0;top:1313px;width:1010px;height:265px;background:var(--pink);color:#fff;text-align:center}
.welcome h2{margin-top:45px;font-family:"Raleway",sans-serif;font-weight:700;font-size:19px}
.welcome p{margin:19px auto 0;width:850px;font-size:12px;line-height:28px}
.searches{position:absolute;left:0;top:1578px;width:1010px;height:182px;background:var(--panel);text-align:center}
.searches h2{margin-top:40px;font-family:"Raleway",sans-serif;font-weight:700;font-size:19px;color:#222}
.tags{margin:22px auto 0;width:930px;font-size:12.5px;color:#444;line-height:34px;text-align:center}
.tags span{margin-right:13px;white-space:nowrap}
.tags span::before{content:"";display:inline-block;width:6px;height:6px;border-radius:50%;background:#999;
  margin-right:6px;vertical-align:middle}
.comments{position:absolute;left:26px;top:1803px;width:957px}
.comments h3{font-family:"Raleway",sans-serif;font-weight:800;font-size:15px;color:#222}
.comment-box{position:relative;margin-top:17px;width:946px;height:157px;border:1px solid #d8dce0;border-radius:3px}
.avatar{position:absolute;left:17px;top:13px;width:82px;height:82px;background:linear-gradient(#cfe3f2,#b6d3ea)}
.comment-field{position:absolute;left:124px;top:13px;width:803px;height:84px;border:1px solid #dde1e5;
  padding:10px 16px;font-size:11px;color:#aaa}
.plugin{position:absolute;left:124px;top:112px;font-size:12px;color:#333;display:flex;align-items:center;gap:10px}
.plugin i{width:13px;height:13px;background:#3b5a96}
.plugin span{text-decoration:underline}
.comment-btn{position:absolute;left:832px;top:106px;width:95px;height:34px;background:var(--pink);color:#fff;
  font-family:"Raleway",sans-serif;font-weight:700;font-size:13px;display:flex;align-items:center;justify-content:center}

.site-footer{position:absolute;left:0;top:2238px;width:1200px;text-align:center}
.follow{display:flex;justify-content:center;align-items:center;gap:5px;font-size:13px;color:#444}
.follow em{font-style:normal;margin-right:8px}
.follow i{width:38px;height:38px;border-radius:50%}
.footer-links{margin-top:18px;font-family:"Raleway",sans-serif;font-weight:700;font-size:13px;color:#222}
.copyright{margin-top:20px;font-size:12px;color:#444}
.meadow{position:absolute;left:0;bottom:0;width:1200px;height:136px;
  background:linear-gradient(#8fd06a,#4f9f2e);border-radius:60% 60% 0 0/40% 40% 0 0}
</style>
</head>
<body>
<div class="top-stripe"></div>
<header class="site-header">
  <div class="brand">LUMEN MUSIC</div>
  <nav class="main-nav"><span>SONG MAP</span><span>ABOUT</span><span>FEATURES</span><span>MY MUSIC</span><span>BROWSE ⌄</span></nav>
  <div class="btn btn-login">LOGIN</div>
  <div class="btn btn-signup">SIGN UP</div>
</header>

<main class="page">
  <nav class="genre-tabs">
    <span class="active">HOME</span><span>RNB</span><span>HIP HOP</span><span>ROCK</span><span>AFRO-POP</span>
    <span class="spread">TOP 20 ARTISTS</span><span class="spread">TOP 20 SONGS</span><span class="spread">VIDEO SONGS</span>
  </nav>
  <div class="search-bar">
    <div class="radio checked"><i></i>ALL</div>
    <div class="radio"><i></i>ARTIST</div>
    <div class="radio"><i></i>SONGS</div>
    <div class="search-input"></div>
    <div class="search-btn">SEARCH</div>
  </div>
  <div class="alphabet">Browse All Songs By Alphabet &nbsp;:
    <div class="letters"><span>0-9</span><span>A</span><span>B</span><span>C</span><span>D</span><span>E</span><span>F</span><span>G</span><span>H</span><span>I</span><span>J</span><span>K</span><span>L</span><span>M</span><span>N</span><span>O</span><span>P</span><span>Q</span><span>R</span><span>S</span><span>T</span><span>U</span><span>V</span><span>W</span><span>X</span><span>Y</span><span>Z</span></div>
  </div>

  <div class="section-bar bar-newest">NEWEST SONGS<div class="arrows"><span>‹</span><span>›</span></div></div>
  <div class="track-row row-newest">
    <div class="track"><div class="art" role="img" aria-label="Singer silhouette with sunburst" style="background:linear-gradient(135deg,#8a8a5a,#2d2d1f)"></div><h4>Finibus Bon <small>(Mp3 Songs)</small></h4><div class="rating"><b>★★★★★</b>(7 Reviews)</div></div>
    <div class="track"><div class="art" role="img" aria-label="Colourful speakers abstract" style="background:linear-gradient(135deg,#1d2d1a,#6a8a2a,#a03a5a)"></div><h4>Finibus Bon <small>(Mp3 Songs)</small></h4><div class="rating"><b>★★★★★</b>(7 Reviews)</div></div>
    <div class="track"><div class="art" role="img" aria-label="Woman with headphones" style="background:linear-gradient(135deg,#d8d8d8,#7a6a6a)"></div><h4>Finibus Bon <small>(Mp3 Songs)</small></h4><div class="rating"><b>★★★★★</b>(7 Reviews)</div></div>
    <div class="track"><div class="art" role="img" aria-label="DJ hands on turntable" style="background:linear-gradient(135deg,#1d3a4a,#6aaac8)"></div><h4>Finibus Bon <small>(Mp3 Songs)</small></h4><div class="rating"><b>★★★★★</b>(7 Reviews)</div></div>
    <div class="track"><div class="art" role="img" aria-label="Pink music abstract" style="background:linear-gradient(135deg,#5a1d6a,#e03a8a)"></div><h4>Finibus Bon <small>(Mp3 Songs)</small></h4><div class="rating"><b>★★★★★</b>(7 Reviews)</div></div>
  </div>

  <div class="section-bar bar-videos">HD VIDEOS SONGS<div class="arrows"><span>‹</span><span>›</span></div></div>
  <div class="track-row row-videos">
    <div class="track"><div class="art" role="img" aria-label="Friends dancing at party" style="background:linear-gradient(135deg,#8a8a8a,#3a3a3a)"></div><h4>Finibus Bon <small>(Mp3 Songs)</small></h4><div class="rating"><b>★★★★★</b>(7 Reviews)</div></div>
    <div class="track"><div class="art" role="img" aria-label="Concert crowd" style="background:linear-gradient(135deg,#1a2a3a,#3a5a6a)"></div><h4>Finibus Bon <small>(Mp4 Songs)</small></h4><div class="rating"><b>★★★★★</b>(7 Reviews)</div></div>
    <div class="track"><div class="art" role="img" aria-label="Woman beside a train carriage" style="background:linear-gradient(135deg,#2a5a3a,#9aa88a)"></div><h4>Finibus Bon <small>(Mp4 Songs)</small></h4><div class="rating"><b>★★★★★</b>(7 Reviews)</div></div>
    <div class="track"><div class="art" role="img" aria-label="Knights on horseback" style="background:linear-gradient(135deg,#a8aab0,#6a5a4a)"></div><h4>Finibus Bon <small>(Mp4 Songs)</small></h4><div class="rating"><b>★★★★★</b>(7 Reviews)</div></div>
    <div class="track"><div class="art" role="img" aria-label="Person with yellow umbrella at sea" style="background:linear-gradient(#a8b0b8,#5a6a72)"></div><h4>Finibus Bon <small>(Mp4 Songs)</small></h4><div class="rating"><b>★★★★★</b>(7 Reviews)</div></div>
  </div>

  <div class="divider"></div>

  <section class="list-box box-artists">
    <h3>ARTISTS</h3>
    <div class="cols">
      <ul><li>Nova Ridge</li><li>Kestrel Vane</li><li>Milo Harte</li><li>Orin Calloway</li><li>Sable Quinn</li><li>The Driftwoods</li><li>Juno Ellery</li><li>Theo Marchetti</li><li>Wren Astley</li></ul>
      <ul><li>Nova Ridge</li><li>Kestrel Vane</li><li>Milo Harte</li><li>Orin Calloway</li><li>Sable Quinn</li><li>The Driftwoods</li><li>Juno Ellery</li><li>Theo Marchetti</li><li>Wren Astley</li></ul>
      <ul><li>The Driftwoods</li><li>Juno Ellery</li><li>Theo Marchetti</li><li>Wren Astley</li></ul>
    </div>
  </section>
  <section class="list-box box-songs">
    <h3>SONGS</h3>
    <div class="cols">
      <ul><li>Nova Ridge</li><li>Kestrel Vane</li><li>Milo Harte</li><li>Orin Calloway</li><li>Sable Quinn</li><li>The Driftwoods</li><li>Juno Ellery</li><li>Theo Marchetti</li><li>Wren Astley</li></ul>
      <ul><li>Nova Ridge</li><li>Kestrel Vane</li><li>Milo Harte</li><li>Orin Calloway</li><li>Sable Quinn</li><li>The Driftwoods</li><li>Juno Ellery</li><li>Theo Marchetti</li><li>Wren Astley</li></ul>
      <ul><li>The Driftwoods</li><li>Juno Ellery</li><li>Theo Marchetti</li><li>Wren Astley</li></ul>
    </div>
  </section>

  <section class="welcome">
    <h2>WELCOME TO LUMEN MUSIC</h2>
    <p>At vero eos et accusamus et iusto odio dignissimos ducimus qui blanditiis praesentium voluptatum deleniti atque corrupti quos dolores et quas molestias excepturi sint occaecati cupiditate non provident, similique sunt in culpa qui officia deserunt mollitia animi, id est laborum et dolorum fuga. Et harum quidem rerum facilis est et expedita distinctio. Nam libero tempore, cum soluta nobis est eligendi optio cumque nihil impedit quo minus id quod maxime placeat facere possimus, omnis voluptas assumenda est, omnis dolor repellendus. Temporibus autem quibusdam et aut officiis debitis aut rerum necessitatibus saepe eveniet ut et voluptates repudiandae sint et molestiae</p>
  </section>

  <section class="searches">
    <h2>LAST SEARCHES</h2>
    <div class="tags"><span>Fire Cars</span><span>Echo Ft Little Rook</span><span>Life Of Birds</span><span>Bees Butterflies</span><span>Etc 'ili Orvane</span><span>Quiet Harbour</span><span>Feat Velora</span><span>Humm Street Life</span><span>Ext Remix Chartline</span><span>Top Hits Paper Lanterns</span><span>Thile Marisol Vey</span><span>Korvel Dj Stop</span><span>One Harbor Under</span><span>A Lantern Harlan Gwen Tobi Kade</span></div>
  </section>

  <section class="comments">
    <h3>COMMENT</h3>
    <div class="comment-box">
      <div class="avatar" role="img" aria-label="Default user avatar"></div>
      <div class="comment-field">ADD A COMMENT ..</div>
      <div class="plugin"><i></i><span>Social comment plugin</span></div>
      <div class="comment-btn">COMMENT</div>
    </div>
  </section>
</main>

<footer class="site-footer">
  <div class="follow"><em>Follow Us On :</em>
    <i style="background:#3b5a96"></i><i style="background:#dd4b39"></i><i style="background:#2aa9e0"></i><i style="background:#c8102e"></i><i style="background:#8a5a3a"></i><i style="background:#d42a2a"></i>
  </div>
  <div class="footer-links">Home &nbsp;| &nbsp;About Us &nbsp;| &nbsp;Recently Mp3 Added &nbsp;| &nbsp;Song Map &nbsp;| &nbsp;About &nbsp;| &nbsp;Features &nbsp;| &nbsp;My Music &nbsp;| &nbsp;Browse ⌄ &nbsp;| &nbsp;Contact</div>
  <div class="copyright">Copyrights © 2016, Lumen Music. All rights reserved.</div>
</footer>
<div class="meadow" role="img" aria-label="Green meadow with grass and floating music notes"></div>
</body>
</html>
```